Business Card Design for Marketing Firm

Looking for business card design for higher end marketing firm. Clean but impressionable/trendy. We are a marketing firm that represents manufacturers in the foodservice equipment and supply industry. Our customers are end users such has hotels, restaurants, country clubs, convention centers and casinos as well as distributors of restaurants supplies and equipment, and manufacturers of foodservice equipment and supplies.
Target Market(s)
Hotels, Restaurants, Supply & Equipment Distributors, Foodservice Manufacturers
Industry/Entity Type
Foodservice/Hospitality
Contact Information for Business Card
Name, Title, Contact Number, Email, Website, Social Media, Address
Requirements
Must have
- Clean & Simple but Serious and Impressionable

```html
<!DOCTYPE html>
<html lang="en">
<head>
<meta charset="utf-8">
<title>Meridian Service Reps – Business Card</title>
<link href="https://fonts.googleapis.com/css2?family=Cinzel:wght@500&family=Noto+Serif:wght@700&family=Arimo&display=swap" rel="stylesheet">
<style>
  :root {
    --backdrop: #1d1d1f;
    --paper: #f3f3f4;
    --navy: #23296b;
    --navy-card: #252b6a;
    --ink: #2e2e33;
    --faint-on-paper: #e2e3e9;
    --faint-on-navy: rgba(255,255,255,0.08);
    --white: #ffffff;
  }
  * { margin: 0; padding: 0; box-sizing: border-box; }
  html, body { width: 1200px; height: 1059px; overflow: hidden; background: var(--backdrop); }
  .stage { position: relative; width: 1200px; height: 1059px; }

  .card { position: absolute; border-radius: 16px; overflow: hidden; }
  .card-front { left: 256px; top: 89px; width: 688px; height: 390px; background: var(--paper); }
  .card-back { left: 254px; top: 547px; width: 693px; height: 393px; background: var(--navy-card); }

  .wordmark { font-family: "Cinzel", serif; font-weight: 500; color: var(--navy); }
  .wordmark .main { display: block; letter-spacing: 0.5px; white-space: nowrap; }
  .wordmark .sub-row { display: flex; align-items: center; gap: 8px; }
  .wordmark .rule { flex: 1; height: 1.5px; background: currentColor; }

  .front-mark { position: absolute; left: 40px; top: 32px; width: 240px; }
  .front-mark .badge { display: block; width: 46px; height: 46px; margin: 0 auto 20px; border: 2px solid var(--navy); border-radius: 50%; }
  .front-mark .main { font-size: 22px; }
  .front-mark .sub { font-size: 14px; }

  .deco-circle { position: absolute; border-radius: 50%; }
  .card-front .deco-circle { right: -60px; bottom: -110px; width: 320px; height: 320px; border: 14px solid var(--faint-on-paper); }
  .card-back .deco-circle { left: 40px; top: -70px; width: 460px; height: 460px; border: 22px solid var(--faint-on-navy); }

  .person { position: absolute; right: 41px; top: 66px; text-align: right; }
  .person .name { font-family: "Noto Serif", serif; font-weight: 700; font-size: 24px; color: var(--navy); letter-spacing: 0.3px; }
  .person .role { font-family: "Arimo", sans-serif; font-size: 16px; color: var(--ink); margin-top: 1px; }
  .tab { position: absolute; right: 0; top: 69px; width: 21px; height: 39px; background: var(--navy); }

  .contact { position: absolute; left: 39px; top: 208px; font-family: "Arimo", sans-serif; color: var(--ink); font-size: 16px; }
  .contact address { font-style: normal; line-height: 20px; margin-bottom: 13px; }
  .contact ul { list-style: none; }
  .contact li { display: flex; align-items: center; gap: 7px; height: 23.5px; }
  .contact svg { width: 12px; height: 12px; fill: var(--navy); flex: none; }
  .dot { width: 11px; height: 11px; border-radius: 50%; background: var(--navy); flex: none; }

  .back-mark { position: absolute; left: 50%; top: 140px; transform: translateX(-50%); width: 390px; color: var(--white); }
  .back-mark .badge { display: block; width: 74px; height: 74px; margin: 0 auto 38px; border: 3px solid var(--white); border-radius: 50%; }
  .back-mark .main { font-size: 33px; }
  .back-mark .sub { font-size: 24px; }
  .back-mark .rule { height: 2px; }
</style>
</head>
<body>
<div class="stage">

  <section class="card card-front">
    <div class="deco-circle" aria-hidden="true"></div>
    <div class="front-mark wordmark">
      <span class="badge" aria-hidden="true"></span>
      <span class="main">Meridian Service</span>
      <span class="sub-row"><span class="rule"></span><span class="sub">Reps</span></span>
    </div>

    <div class="person">
      <div class="name">DANIEL WHITFORD</div>
      <div class="role">CEO/Founder</div>
    </div>
    <div class="tab"></div>

    <div class="contact">
      <address>456 Harbor Lane, Suite 210<br>Lakeview City, AB 42150</address>
      <ul>
        <li><svg viewBox="0 0 12 12"><path d="M1 4c0-2 2-3 5-3s5 1 5 3v1H8.5V3.8h-5V5H1zM2 6h8l1 5H1z"/></svg>555-204-7731</li>
        <li><svg viewBox="0 0 12 12"><path d="M6 .5 11.5 5v6.5H.5V5zM2 6v4.5h8V6L6 8.5z"/></svg>hello@meridianservicereps.com</li>
        <li><svg viewBox="0 0 12 12"><circle cx="6" cy="6" r="5.5"/><path d="M3 3.5 5 3l1 2-2 1.5zM7 7l2.5-.5L8 10z" fill="#f3f3f4"/></svg>www.meridianservicereps.com</li>
        <li><span class="dot"></span>@meridianservicereps</li>
      </ul>
    </div>
  </section>

  <section class="card card-back">
    <div class="deco-circle" aria-hidden="true"></div>
    <div class="back-mark wordmark">
      <span class="badge" aria-hidden="true"></span>
      <span class="main">Meridian Service</span>
      <span class="sub-row"><span class="rule"></span><span class="sub">Reps</span></span>
    </div>
  </section>

</div>
</body>
</html>
```